Fire Risk Assessment App needs a sleek UI design

I need a sleek, modern but professional design for my 5 page Fire Risk Assessment App. Include gradient background, fire themed colours including reds, yellows, light orange and a touch of black. Design must ooze simplicity and professionalism. This is for the UK market. See attached images and word doc for more information.

Target Market(s)

General public and business owners

Industry/Entity Type

Technology / Fire Safety

Colors
00AB8E
00BBA5
67D7C9
C6EFE9
E9F9F6
59FF00
82FF00
B8FF75
E3FFCB
F4FFEA
FFC000
F8CF3A
FAE287
FDF2CF
FEFAEE
F0912C
F2A743
F7CA91
FBE8D2
FDF5EE
EE7325
F08F49
F5BC92
FAE3D3
FDF4ED
EB3D1F
EC4F4E
F09395
F8D3D4
FCEDEE

```html
<!DOCTYPE html>
<html lang="en">
<head>
<meta charset="utf-8">
<title>Fire Risk Assessment App – Screens</title>
<link href="https://fonts.googleapis.com/css2?family=Poppins:wght@400;500;600;700&display=swap" rel="stylesheet">
<style>
:root{
  --bg:#2c1111;
  --red:#eb3d1f;
  --red-deep:#c8281c;
  --orange:#ee7325;
  --orange-light:#f08f49;
  --yellow:#ffc000;
  --label:#ee7325;
  --white:#ffffff;
  --ink:#1d1d1d;
  --muted:#8a8a8a;
  --line:#ececec;
  --tint:#fcedee;
  --green:#00ab8e;
  --green-tint:#e9f9f6;
  --frame:#0c0c0c;
}
*{box-sizing:border-box;margin:0;padding:0}
html,body{width:1200px;height:2496px;overflow:hidden}
body{background:var(--bg);font-family:'Poppins',sans-serif;position:relative;color:var(--white)}
.phone{position:absolute;width:292px;height:620px;background:var(--frame);border-radius:46px;padding:7px}
.screen{position:relative;width:100%;height:100%;border-radius:39px;overflow:hidden;background:linear-gradient(180deg,var(--red) 0%,var(--red-deep) 100%)}
.status{position:absolute;top:14px;left:24px;right:20px;display:flex;justify-content:space-between;font-size:10px;font-weight:600}
.status-icons{display:flex;gap:4px;align-items:center}
.app-header{position:absolute;top:40px;left:14px;right:16px;display:flex;align-items:center;gap:8px;font-size:13.5px;font-weight:700}
.app-header .user{margin-left:auto}
.card{position:absolute;left:14px;right:14px;background:var(--white);border-radius:6px;color:var(--ink)}
.card-head{display:flex;justify-content:space-between;padding:11px 11px 0;font-size:8.5px;font-weight:600}
.card-head .link{color:var(--red);font-size:7px;font-weight:600}
.item{display:flex;align-items:center;gap:10px;border:1px solid var(--line);border-radius:5px;margin:8px 11px 0;padding:8px 10px;height:52px}
.item-title{font-size:8.5px;font-weight:600;color:var(--ink)}
.item-sub{font-size:6.5px;color:var(--muted)}
.chev{margin-left:auto;color:var(--red);font-size:10px}
.badge{display:inline-flex;align-items:center;gap:3px;font-size:5.5px;font-weight:600;border-radius:3px;padding:1px 4px;margin-top:2px}
.badge.progress{background:#fdf2cf;color:var(--orange)}
.badge.done{background:var(--green-tint);color:var(--green)}
.badge i{width:6px;height:6px;border-radius:50%;display:inline-block}
.badge.progress i{background:var(--orange)}
.badge.done i{background:var(--green)}
.prop-icon{width:26px;height:26px;border-radius:50%;background:var(--tint);display:flex;align-items:center;justify-content:center;flex:none}
.dots{display:flex;justify-content:center;gap:3px;margin-top:7px}
.dots span{width:3px;height:3px;border-radius:2px;background:#f8d3d4}
.dots span.on{width:20px;background:var(--red)}
.add-btn{margin:10px 11px 0;height:26px;border-radius:14px;background:linear-gradient(90deg,var(--orange),var(--red));color:var(--white);font-size:9px;font-weight:600;display:flex;align-items:center;justify-content:center;gap:6px}
.section-title{position:absolute;left:14px;font-size:11.5px;font-weight:600}
.row{position:absolute;left:14px;right:14px;height:50px;background:var(--white);border-radius:4px;color:var(--ink);display:flex;align-items:center;gap:12px;padding:0 14px}
.pill-link{position:absolute;left:50%;transform:translateX(-50%);height:20px;padding:0 8px;border:1px solid var(--white);border-radius:12px;font-size:7.5px;font-weight:600;display:flex;align-items:center;gap:6px;white-space:nowrap}
.history{position:absolute;left:14px;right:14px;display:flex;gap:12px;align-items:center}
.history .h-title{font-size:8px;font-weight:600}
.history .h-sub{font-size:6.5px;opacity:.8}
.nav{position:absolute;left:0;right:0;bottom:0;height:62px;background:var(--white);display:flex;justify-content:space-around;padding-top:8px;color:#c9a9a4}
.nav-item{display:flex;flex-direction:column;align-items:center;gap:2px;font-size:5.5px;width:40px}
.nav-item.active{color:var(--red);font-weight:600}
.home-bar{position:absolute;left:50%;bottom:8px;transform:translateX(-50%);width:104px;height:3px;border-radius:2px;background:var(--ink)}
.home-bar.light{background:var(--white)}
.light-body{position:absolute;left:0;right:0;top:205px;bottom:0;background:var(--white)}
.alt2 .section-title,.alt2 .history{color:var(--ink)}
.alt2 .row{border:1px solid var(--line)}
.alt2 .pill-link{border-color:var(--red);color:var(--red)}
.alt2 .history .h-sub{color:var(--muted)}
.alt2 .divider{position:absolute;left:14px;right:14px;height:1px;background:var(--line)}
.prompt{position:absolute;top:150px;left:14px;font-size:9px;font-weight:600}
.choice{position:absolute;left:14px;right:14px;height:50px;border-radius:26px;border:1.5px solid var(--white);display:flex;align-items:center;gap:14px;padding:0 10px;font-size:9.5px;font-weight:600}
.choice.selected{background:var(--white);color:var(--red)}
.choice .tick{margin-left:auto}
.flame-art{position:absolute;left:40px;top:275px;width:216px;height:216px;border-radius:50%;background:radial-gradient(circle,rgba(255,255,255,.2) 0%,rgba(255,255,255,.1) 60%,rgba(255,255,255,.06) 100%)}
.actions{position:absolute;left:14px;right:14px;top:525px;display:flex;gap:12px}
.btn{flex:1;height:34px;border-radius:18px;display:flex;align-items:center;justify-content:center;gap:10px;font-size:9.5px;font-weight:600}
.btn.ghost{border:1.5px solid var(--white)}
.btn.solid{background:var(--white);color:var(--red)}
.vlabel{position:absolute;transform-origin:left top;transform:rotate(-90deg);color:var(--label);font-size:12px;letter-spacing:7px;white-space:nowrap;font-weight:500}
.connectors{position:absolute;left:0;top:0}
</style>
</head>
<body>

<svg class="connectors" width="1200" height="2496" viewBox="0 0 1200 2496" fill="none" stroke="#ffc000" stroke-width="1.5">
  <polyline points="510,1118 583,1118 583,1560"/>
  <polyline points="413,1482 413,1560 792,1560 792,1524"/>
  <polyline points="786,1530 792,1523 798,1530"/>
  <polyline points="413,2261 413,2338 792,2338 792,2303"/>
  <polyline points="786,2309 792,2302 798,2309"/>
  <circle cx="510" cy="1118" r="3.5" fill="#ffc000" stroke="none"/>
  <circle cx="413" cy="1482" r="3.5" fill="#ffc000" stroke="none"/>
  <circle cx="413" cy="2261" r="3.5" fill="#ffc000" stroke="none"/>
</svg>

<div class="vlabel" style="left:242px;top:1235px">DASHBOARD DESIGN ALT 1</div>
<div class="vlabel" style="left:613px;top:1185px">ADD NEW ASSESSMENT</div>
<div class="vlabel" style="left:242px;top:2012px">DASHBOARD DESIGN ALT 2</div>
<div class="vlabel" style="left:613px;top:2004px">ADD NEW ASSESSMENT V2</div>

<!-- Dashboard alt 1 -->
<div class="phone" style="left:268px;top:908px">
  <div class="screen">
    <div class="status"><span>9:41</span><span class="status-icons"><svg width="12" height="8"><rect x="0" y="5" width="2" height="3" fill="#fff"/><rect x="3" y="3" width="2" height="5" fill="#fff"/><rect x="6" y="1" width="2" height="7" fill="#fff"/><rect x="9" y="0" width="2" height="8" fill="#fff"/></svg><svg width="16" height="8"><rect x="0.5" y="0.5" width="13" height="7" rx="2" stroke="#fff" fill="none"/><rect x="2" y="2" width="10" height="4" rx="1" fill="#fff"/></svg></span></div>
    <div class="app-header"><svg width="18" height="18" viewBox="0 0 18 18"><circle cx="9" cy="9" r="8" fill="none" stroke="#fff" stroke-width="2"/><path d="M9 10 L13 5" stroke="#fff" stroke-width="2" stroke-linecap="round"/></svg>Dashboard<svg class="user" width="18" height="18" viewBox="0 0 18 18"><circle cx="9" cy="9" r="9" fill="#fff"/><circle cx="9" cy="7" r="3" fill="#d8301e"/><path d="M3.5 14.5c1.5-3 9.5-3 11 0" fill="#d8301e"/></svg></div>
    <div class="card" style="top:78px;height:155px">
      <div class="card-head"><span>Fire Risk Assessments</span><span class="link">VIEW ALL</span></div>
      <div class="item"><div class="prop-icon"><svg width="12" height="12"><rect x="2" y="1" width="8" height="11" fill="#eb3d1f"/></svg></div><div><div class="item-title">Hartley Residence</div><div class="item-sub">Section 7.01 / 30.00</div><span class="badge progress"><i></i>IN-PROGRESS</span></div><span class="chev">›</span></div>
      <div class="dots"><span class="on"></span><span></span><span></span><span></span></div>
      <div class="add-btn"><svg width="9" height="11" viewBox="0 0 9 11"><path d="M4.5 0C6 3 9 4.5 9 7.2A4.5 4.5 0 0 1 0 7.2C0 5 2 4 2 2 3 3 3.5 3.5 3.5 4.5 4.5 3 4.5 1.5 4.5 0Z" fill="#fff"/></svg>Add new assessment</div>
    </div>
    <div class="section-title" style="top:264px">Completed Assessments</div>
    <div class="row" style="top:290px"><svg width="16" height="16"><rect x="2" y="2" width="12" height="13" fill="#eb3d1f"/></svg><div><div class="item-title">Willow Court Care Home</div><span class="badge done"><i></i>COMPLETED</span></div><span class="chev">›</span></div>
    <div class="row" style="top:345px"><svg width="16" height="16"><rect x="3" y="2" width="10" height="13" fill="#eb3d1f"/></svg><div><div class="item-title">The Meadow Residences</div><span class="badge done"><i></i>COMPLETED</span></div><span class="chev">›</span></div>
    <div class="pill-link" style="top:405px">View all completed <span>→</span></div>
    <div class="section-title" style="top:455px">Purchase History</div>
    <div class="history" style="top:483px"><svg width="20" height="20"><circle cx="10" cy="10" r="10" fill="#fff"/><rect x="6" y="5" width="8" height="10" fill="#eb3d1f"/></svg><div><div class="h-title">Residential Fire Risk Assessments</div><div class="h-sub">Sun, 12 July 2024 • 16:20:32</div></div></div>
    <div class="history" style="top:530px"><svg width="20" height="20"><circle cx="10" cy="10" r="10" fill="#fff"/></svg><div><div class="h-title">Commercial Fire Risk Assessments</div></div></div>
    <div class="nav">
      <div class="nav-item active"><svg width="14" height="14"><circle cx="7" cy="7" r="6" fill="none" stroke="#eb3d1f" stroke-width="2"/></svg>Dashboard</div>
      <div class="nav-item"><svg width="16" height="12"><rect x="1" y="1" width="14" height="10" rx="2" fill="none" stroke="currentColor"/></svg>Purchases</div>
      <div class="nav-item"><svg width="16" height="20" viewBox="0 0 9 11"><path d="M4.5 0C6 3 9 4.5 9 7.2A4.5 4.5 0 0 1 0 7.2C0 5 2 4 2 2 3 3 3.5 3.5 3.5 4.5 4.5 3 4.5 1.5 4.5 0Z" fill="#ee7325"/></svg></div>
      <div class="nav-item"><svg width="14" height="14"><circle cx="7" cy="7" r="6" fill="none" stroke="currentColor"/></svg>Support</div>
      <div class="nav-item"><svg width="12" height="14"><rect x="1" y="1" width="10" height="12" fill="none" stroke="currentColor"/></svg>Logout</div>
    </div>
    <div class="home-bar"></div>
  </div>
</div>

<!-- Add new assessment -->
<div class="phone" style="left:641px;top:908px">
  <div class="screen">
    <div class="status"><span>9:41</span><span class="status-icons"><svg width="12" height="8"><rect x="0" y="5" width="2" height="3" fill="#fff"/><rect x="3" y="3" width="2" height="5" fill="#fff"/><rect x="6" y="1" width="2" height="7" fill="#fff"/><rect x="9" y="0" width="2" height="8" fill="#fff"/></svg><svg width="16" height="8"><rect x="0.5" y="0.5" width="13" height="7" rx="2" stroke="#fff" fill="none"/><rect x="2" y="2" width="10" height="4" rx="1" fill="#fff"/></svg></span></div>
    <div class="app-header"><svg width="16" height="20" viewBox="0 0 9 11"><path d="M4.5 0C6 3 9 4.5 9 7.2A4.5 4.5 0 0 1 0 7.2C0 5 2 4 2 2 3 3 3.5 3.5 3.5 4.5 4.5 3 4.5 1.5 4.5 0Z" fill="#fff"/></svg>Add Fire Risk Assessment</div>
    <div class="prompt">Select type of property</div>
    <div class="flame-art" role="img" aria-label="Large faint flame emblem"></div>
    <div class="choice" style="top:172px"><svg width="28" height="28"><circle cx="14" cy="14" r="14" fill="#fff"/><rect x="9" y="8" width="10" height="13" fill="#eb3d1f"/></svg>Residential</div>
    <div class="choice selected" style="top:229px"><svg width="28" height="28"><circle cx="14" cy="14" r="14" fill="#fcedee"/><rect x="8" y="8" width="12" height="13" fill="#eb3d1f"/></svg>Commercial<svg class="tick" width="14" height="14"><circle cx="7" cy="7" r="7" fill="#eb3d1f"/><path d="M4 7l2 2 4-4" stroke="#fff" stroke-width="1.6" fill="none"/></svg></div>
    <div class="actions"><div class="btn ghost"><span>✕</span>Cancel</div><div class="btn solid">Continue <span>→</span></div></div>
    <div class="home-bar light"></div>
  </div>
</div>

<!-- Dashboard alt 2 -->
<div class="phone alt2" style="left:268px;top:1686px">
  <div class="screen">
    <div class="light-body"></div>
    <div class="status"><span>9:41</span><span class="status-icons"><svg width="12" height="8"><rect x="0" y="5" width="2" height="3" fill="#fff"/><rect x="3" y="3" width="2" height="5" fill="#fff"/><rect x="6" y="1" width="2" height="7" fill="#fff"/><rect x="9" y="0" width="2" height="8" fill="#fff"/></svg><svg width="16" height="8"><rect x="0.5" y="0.5" width="13" height="7" rx="2" stroke="#fff" fill="none"/><rect x="2" y="2" width="10" height="4" rx="1" fill="#fff"/></svg></span></div>
    <div class="app-header"><svg width="18" height="18" viewBox="0 0 18 18"><circle cx="9" cy="9" r="8" fill="none" stroke="#fff" stroke-width="2"/><path d="M9 10 L13 5" stroke="#fff" stroke-width="2" stroke-linecap="round"/></svg>Dashboard<svg class="user" width="18" height="18" viewBox="0 0 18 18"><circle cx="9" cy="9" r="9" fill="#fff"/><circle cx="9" cy="7" r="3" fill="#d8301e"/><path d="M3.5 14.5c1.5-3 9.5-3 11 0" fill="#d8301e"/></svg></div>
    <div class="card" style="top:78px;height:115px">
      <div class="card-head"><span>Fire Risk Assessments</span><span class="link">VIEW ALL</span></div>
      <div class="item"><svg width="24" height="22"><path d="M2 11 L12 2 L22 11 V21 H2Z" fill="#f08f49"/></svg><div><div class="item-title">Hartley Residence</div><div class="item-sub">Section 7.01 / 30.00</div><span class="badge progress"><i></i>IN-PROGRESS</span></div><span class="chev">›</span></div>
      <div class="dots"><span class="on"></span><span></span><span></span><span></span></div>
    </div>
    <div class="section-title" style="top:223px">Completed Assessments</div>
    <div class="row" style="top:248px"><svg width="22" height="20"><rect x="1" y="2" width="20" height="17" fill="#2b5a86"/></svg><div><div class="item-title">Willow Court Care Home</div><span class="badge done"><i></i>COMPLETED</span></div><span class="chev">›</span></div>
    <div class="row" style="top:303px"><svg width="22" height="20"><path d="M1 10 L11 1 L21 10 V19 H1Z" fill="#f08f49"/></svg><div><div class="item-title">The Meadow Residences</div><span class="badge done"><i></i>COMPLETED</span></div><span class="chev">›</span></div>
    <div class="pill-link" style="top:364px">View all completed <span>→</span></div>
    <div class="section-title" style="top:414px">Purchase History</div>
    <div class="history" style="top:444px"><svg width="20" height="20"><path d="M1 10 L10 2 L19 10 V19 H1Z" fill="#f08f49"/></svg><div><div class="h-title">Residential Fire Risk Assessments</div><div class="h-sub">Sun, 12 July 2024 • 16:20:32</div></div></div>
    <div class="divider" style="top:480px"></div>
    <div class="history" style="top:489px"><svg width="20" height="20"><rect x="1" y="2" width="18" height="16" fill="#2b5a86"/></svg><div><div class="h-title">Commercial Fire Risk Assessments</div><div class="h-sub">Sat, 6 July 2024 • 10:48:57</div></div></div>
    <div class="nav" style="border-top:1.5px solid var(--red)">
      <div class="nav-item active"><svg width="14" height="14"><circle cx="7" cy="7" r="6" fill="none" stroke="#eb3d1f" stroke-width="2"/></svg>Dashboard</div>
      <div class="nav-item"><svg width="16" height="12"><rect x="1" y="1" width="14" height="10" rx="2" fill="none" stroke="currentColor"/></svg>Purchases</div>
      <div class="nav-item"><svg width="16" height="20" viewBox="0 0 9 11"><path d="M4.5 0C6 3 9 4.5 9 7.2A4.5 4.5 0 0 1 0 7.2C0 5 2 4 2 2 3 3 3.5 3.5 3.5 4.5 4.5 3 4.5 1.5 4.5 0Z" fill="#ee7325"/></svg></div>
      <div class="nav-item"><svg width="14" height="14"><circle cx="7" cy="7" r="6" fill="none" stroke="currentColor"/></svg>Support</div>
      <div class="nav-item"><svg width="12" height="14"><rect x="1" y="1" width="10" height="12" fill="none" stroke="currentColor"/></svg>Logout</div>
    </div>
    <div class="home-bar"></div>
  </div>
</div>

<!-- Add new assessment v2 -->
<div class="phone" style="left:641px;top:1686px">
  <div class="screen">
    <div class="status"><span>9:41</span><span class="status-icons"><svg width="12" height="8"><rect x="0" y="5" width="2" height="3" fill="#fff"/><rect x="3" y="3" width="2" height="5" fill="#fff"/><rect x="6" y="1" width="2" height="7" fill="#fff"/><rect x="9" y="0" width="2" height="8" fill="#fff"/></svg><svg width="16" height="8"><rect x="0.5" y="0.5" width="13" height="7" rx="2" stroke="#fff" fill="none"/><rect x="2" y="2" width="10" height="4" rx="1" fill="#fff"/></svg></span></div>
    <div class="app-header"><svg width="16" height="20" viewBox="0 0 9 11"><path d="M4.5 0C6 3 9 4.5 9 7.2A4.5 4.5 0 0 1 0 7.2C0 5 2 4 2 2 3 3 3.5 3.5 3.5 4.5 4.5 3 4.5 1.5 4.5 0Z" fill="#fff"/></svg>Add Fire Risk Assessment</div>
    <div class="prompt">Select type of property</div>
    <div class="flame-art" role="img" aria-label="Large faint flame emblem"></div>
    <div class="choice" style="top:172px"><svg width="26" height="24"><path d="M1 12 L13 2 L25 12 V23 H1Z" fill="#f08f49"/></svg>Residential</div>
    <div class="choice selected" style="top:229px"><svg width="26" height="24"><rect x="2" y="2" width="22" height="20" fill="#2b5a86"/></svg>Commercial<svg class="tick" width="14" height="14"><circle cx="7" cy="7" r="7" fill="#eb3d1f"/><path d="M4 7l2 2 4-4" stroke="#fff" stroke-width="1.6" fill="none"/></svg></div>
    <div class="actions"><div class="btn ghost"><span>✕</span>Cancel</div><div class="btn solid">Continue <span>→</span></div></div>
    <div class="home-bar light"></div>
  </div>
</div>

</body>
</html>
```